WebApp for IoT (Vexa lights and Kirra/Brelline)

I am going to create my own dashbord for Quillet Pro (See other examples on https://quillet.example/) But I want it much more flexible and advanced.
One page per room (So I can have an Zanbo in each room with all functions just for that room) and include controls for light (both overall for the room and in an popupwindow all lightbulbs n the room - se more about how its done in Torvald Vexa app on https://www.torvald-vexa.example/en-us/explore-vexa/apps/bridge) aswell as set volume/track for Kirra.

I want the final solution to be "skinable" so I can choose from Blue-CSS to Green-CSS etc, but at this moment I only want ONE color!

I have added an PDF with the functions I am thinking of, but the design is for you to create!

Please have in mind it will be running on Zanbos on the wall, and in the mobile.

For the moment I only want an PSD of the "Room page", "Light popup" and "Sound Popup", but I might contract the winner to get HTML/CSS as second step.

```html
<!DOCTYPE html>
<html lang="en">
<head>
<meta charset="utf-8">
<title>Room Dashboard</title>
<link rel="stylesheet" href="https://fonts.googleapis.com/css2?family=Lato:wght@400;700&display=swap">
<style>
  :root{
    --page:#e3e3e3;
    --accent:#4471c8;
    --white:#ffffff;
    --ink:#1d1d1f;
    --scene-kitchen-a:#2a2c30;
    --scene-kitchen-b:#111214;
    --scene-bed-a:#2b2624;
    --scene-bed-b:#141211;
    --slider-dark:#6f6f6f;
    --slider-light:#d6d6d6;
    --knob:#bdbdbd;
  }
  *{box-sizing:border-box;margin:0;padding:0}
  html,body{width:873px;height:1200px;overflow:hidden;background:var(--page)}
  body{font-family:"Lato",sans-serif;color:var(--white);position:relative}

  .room-screen{position:absolute;overflow:hidden}
  .room-screen--kitchen{left:112px;top:96px;width:657px;height:413px}
  .room-screen--bedroom{left:84px;top:588px;width:706px;height:528px}
  .scene{position:absolute;inset:0}
  .room-screen--kitchen .scene{background:radial-gradient(ellipse at 55% 55%,var(--scene-kitchen-a),var(--scene-kitchen-b))}
  .room-screen--bedroom .scene{background:radial-gradient(ellipse at 55% 60%,var(--scene-bed-a),var(--scene-bed-b))}

  .abs{position:absolute}

  .room-select{width:145px;height:40px;border:1px solid var(--white);border-radius:20px;
    display:flex;align-items:center;justify-content:space-between;padding:0 18px 0 19px;
    font-size:14px;letter-spacing:.2px}
  .room-select .caret{width:0;height:0;border-left:4px solid transparent;border-right:4px solid transparent;border-top:4px solid var(--white)}

  .status{width:90px;text-align:center;font-size:13px;line-height:18.5px}
  .status .badge{width:42px;height:42px;border-radius:50%;background:var(--accent);margin:0 auto 13px;display:flex;align-items:center;justify-content:center}
  .status .badge svg{width:26px;height:26px}

  .control-icon{width:42px;height:42px;border-radius:50%;background:var(--accent);display:flex;align-items:center;justify-content:center}
  .control-icon svg{width:26px;height:26px}
  .control-label{font-size:13.5px;line-height:17px}

  .toggle{width:51px;height:17px;border-radius:9px;background:var(--white);display:flex;align-items:center;padding:0 3px;font-size:9.5px;font-weight:700}
  .toggle .dot{width:13px;height:13px;border-radius:50%;background:var(--accent)}
  .toggle--on{color:var(--ink);gap:11px}
  .toggle--off{color:var(--accent);justify-content:space-between;padding-left:10px}

  .slider{width:196px;height:37px;border-radius:8px;background:linear-gradient(90deg,var(--slider-dark),var(--slider-light))}
  .slider .knob{position:absolute;top:3px;width:30px;height:30px;border-radius:50%;background:var(--knob);border:2px solid var(--white)}
  .slider .glyph{position:absolute;top:8px;width:21px;height:21px}
  .value{font-size:13px;line-height:16px}

  .device-button{width:123px;height:34px;border-radius:17px;border:1px solid var(--white);display:flex;align-items:center;padding-left:2px;gap:13px;font-size:12.5px}
  .device-button .chip{width:30px;height:30px;border-radius:50%;background:var(--white);display:flex;align-items:center;justify-content:center}
  .device-button .chip svg{width:20px;height:20px}
  .device-button--active{background:var(--white);color:var(--accent)}
  .device-button--active .chip{background:var(--accent)}

  /* kitchen placements */
  .kitchen-select{left:15px;top:21px}
  .kitchen-weather{left:438px;top:21px}
  .kitchen-clock{left:560px;top:21px}
  .kitchen-light-icon{left:16px;top:221px}
  .kitchen-light-label{left:72px;top:233px}
  .kitchen-light-toggle{left:141px;top:234px}
  .kitchen-light-slider{left:16px;top:286px}
  .kitchen-light-value{left:172px;top:335px}
  .kitchen-bulb-1{left:517px;top:229px}
  .kitchen-bulb-2{left:517px;top:284px}
  .kitchen-bulb-3{left:517px;top:346px}

  /* bedroom placements */
  .bedroom-select{left:41px;top:51px}
  .bedroom-weather{left:463px;top:51px}
  .bedroom-clock{left:585px;top:51px}
  .bedroom-light-icon{left:40px;top:235px}
  .bedroom-light-label{left:96px;top:247px}
  .bedroom-light-toggle{left:165px;top:247px}
  .bedroom-light-slider{left:40px;top:300px}
  .bedroom-light-value{left:208px;top:348px}
  .bedroom-volume-icon{left:40px;top:373px}
  .bedroom-volume-label{left:96px;top:385px}
  .bedroom-volume-toggle{left:165px;top:385px}
  .bedroom-volume-slider{left:40px;top:437px}
  .bedroom-volume-value{left:51px;top:492px}
  .bedroom-speaker-1{left:542px;top:235px}
  .bedroom-speaker-2{left:542px;top:296px}
  .bedroom-speaker-3{left:542px;top:356px}
  .bedroom-speaker-4{left:542px;top:417px}
</style>
</head>
<body>

<svg width="0" height="0" style="position:absolute" aria-hidden="true">
  <defs>
    <symbol id="icon-bulb" viewBox="0 0 24 24">
      <g fill="none" stroke="currentColor" stroke-width="1.6" stroke-linecap="round">
        <path d="M12 1.5v2M4.5 4.5l1.4 1.4M19.5 4.5l-1.4 1.4M1.5 12h2M20.5 12h2"/>
      </g>
      <path fill="currentColor" d="M12 6.5a5.3 5.3 0 0 0-3.2 9.5c.6.5.9 1.1.9 1.8h4.6c0-.7.3-1.3.9-1.8A5.3 5.3 0 0 0 12 6.5z"/>
      <rect fill="currentColor" x="9.7" y="18.6" width="4.6" height="1.5" rx=".6"/>
      <rect fill="currentColor" x="10.3" y="20.7" width="3.4" height="1.5" rx=".6"/>
    </symbol>
    <symbol id="icon-sun" viewBox="0 0 24 24">
      <circle cx="12" cy="12" r="5" fill="currentColor"/>
      <g stroke="currentColor" stroke-width="1.8" stroke-linecap="round">
        <path d="M12 1.5v3M12 19.5v3M1.5 12h3M19.5 12h3M4.6 4.6l2 2M17.4 17.4l2 2M4.6 19.4l2-2M17.4 6.6l2-2"/>
      </g>
    </symbol>
    <symbol id="icon-weather" viewBox="0 0 24 24">
      <circle cx="14.5" cy="8.5" r="3.2" fill="currentColor"/>
      <g stroke="currentColor" stroke-width="1.3" stroke-linecap="round">
        <path d="M14.5 2.3v1.4M20.7 8.5h-1.4M18.9 4.1l-1 1M10.1 4.1l1 1M18.9 12.9l-1-1"/>
      </g>
      <path fill="currentColor" d="M7 20.5a4 4 0 0 1-.4-8 5 5 0 0 1 9.4 1.3 3.4 3.4 0 0 1 .6 6.7z"/>
    </symbol>
    <symbol id="icon-clock" viewBox="0 0 24 24">
      <circle cx="12" cy="12" r="10" fill="none" stroke="currentColor" stroke-width="1.6"/>
      <path d="M12 6v6l4 3" fill="none" stroke="currentColor" stroke-width="1.6" stroke-linecap="round"/>
      <g fill="currentColor"><circle cx="12" cy="3.8" r=".8"/><circle cx="12" cy="20.2" r=".8"/><circle cx="3.8" cy="12" r=".8"/><circle cx="20.2" cy="12" r=".8"/></g>
    </symbol>
    <symbol id="icon-speaker" viewBox="0 0 24 24">
      <path fill="currentColor" d="M3 9h4l5-4.5v15L7 15H3z"/>
      <g fill="none" stroke="currentColor" stroke-width="1.6" stroke-linecap="round">
        <path d="M15 9a4 4 0 0 1 0 6M17.5 6.5a7.5 7.5 0 0 1 0 11"/>
      </g>
    </symbol>
    <symbol id="icon-speaker-low" viewBox="0 0 24 24">
      <path fill="currentColor" d="M2 9h4l6-5v16l-6-5H2z"/>
      <path d="M15 12h5" stroke="currentColor" stroke-width="1.8"/>
    </symbol>
  </defs>
</svg>

<!-- Kitchen room page -->
<section class="room-screen room-screen--kitchen">
  <div class="scene" role="img" aria-label="Dimmed photo of a white kitchen with pendant lamps and bar stools"></div>

  <div class="abs room-select kitchen-select"><span>KITCHEN</span><span class="caret"></span></div>

  <div class="abs status kitchen-weather">
    <div class="badge"><svg style="color:var(--white)"><use href="#icon-weather"/></svg></div>
    <div>23° SUNNY</div>
  </div>
  <div class="abs status kitchen-clock">
    <div class="badge"><svg style="color:var(--white)"><use href="#icon-clock"/></svg></div>
    <div>2022-07-14<br>15:23</div>
  </div>

  <div class="abs control-icon kitchen-light-icon"><svg style="color:var(--white)"><use href="#icon-bulb"/></svg></div>
  <div class="abs control-label kitchen-light-label">LIGHT</div>
  <div class="abs toggle toggle--on kitchen-light-toggle"><span class="dot"></span><span>ON</span></div>

  <div class="abs slider kitchen-light-slider">
    <svg class="glyph" style="left:8px;color:var(--white)"><use href="#icon-sun"/></svg>
    <span class="knob" style="left:163px"></span>
  </div>
  <div class="abs value kitchen-light-value">100%</div>

  <div class="abs device-button device-button--active kitchen-bulb-1">
    <span class="chip"><svg style="color:var(--white)"><use href="#icon-bulb"/></svg></span>LIGHT 1
  </div>
  <div class="abs device-button kitchen-bulb-2">
    <span class="chip"><svg style="color:var(--accent)"><use href="#icon-bulb"/></svg></span>LIGHT 2
  </div>
  <div class="abs device-button kitchen-bulb-3">
    <span class="chip"><svg style="color:var(--accent)"><use href="#icon-bulb"/></svg></span>LIGHT 3
  </div>
</section>

<!-- Bedroom room page -->
<section class="room-screen room-screen--bedroom">
  <div class="scene" role="img" aria-label="Dimmed photo of a bedroom with a made bed, wooden slat wall and flowers"></div>

  <div class="abs room-select bedroom-select"><span>BED ROOM</span><span class="caret"></span></div>

  <div class="abs status bedroom-weather">
    <div class="badge"><svg style="color:var(--white)"><use href="#icon-weather"/></svg></div>
    <div>23° SUNNY</div>
  </div>
  <div class="abs status bedroom-clock">
    <div class="badge"><svg style="color:var(--white)"><use href="#icon-clock"/></svg></div>
    <div>2022-07-14<br>15:23</div>
  </div>

  <div class="abs control-icon bedroom-light-icon"><svg style="color:var(--white)"><use href="#icon-bulb"/></svg></div>
  <div class="abs control-label bedroom-light-label">LIGHT</div>
  <div class="abs toggle toggle--off bedroom-light-toggle"><span>OFF</span><span class="dot"></span></div>

  <div class="abs slider bedroom-light-slider">
    <span class="knob" style="left:4px"></span>
    <svg class="glyph" style="left:166px;color:var(--white);opacity:.8"><use href="#icon-sun"/></svg>
  </div>
  <div class="abs value bedroom-light-value">100</div>

  <div class="abs control-icon bedroom-volume-icon"><svg style="color:var(--white)"><use href="#icon-speaker"/></svg></div>
  <div class="abs control-label bedroom-volume-label">VOLUME</div>
  <div class="abs toggle toggle--on bedroom-volume-toggle"><span class="dot"></span><span>ON</span></div>

  <div class="abs slider bedroom-volume-slider">
    <svg class="glyph" style="left:8px;color:var(--white)"><use href="#icon-speaker-low"/></svg>
    <span class="knob" style="left:158px"></span>
  </div>
  <div class="abs value bedroom-volume-value">0</div>

  <div class="abs device-button device-button--active bedroom-speaker-1">
    <span class="chip"><svg style="color:var(--white)"><use href="#icon-speaker"/></svg></span>SPEAKER
  </div>
  <div class="abs device-button bedroom-speaker-2">
    <span class="chip"><svg style="color:var(--accent)"><use href="#icon-speaker"/></svg></span>SPEAKER
  </div>
  <div class="abs device-button bedroom-speaker-3">
    <span class="chip"><svg style="color:var(--accent)"><use href="#icon-speaker"/></svg></span>SPEAKER
  </div>
  <div class="abs device-button bedroom-speaker-4">
    <span class="chip"><svg style="color:var(--accent)"><use href="#icon-speaker"/></svg></span>SPEAKER
  </div>
</section>

</body>
</html>
```